Business card design Needed for new logo / Construction business, home extensions and new builds

We need a business card design using our new logo files which i will attach to this project :)

We are a small construction business specialising in home extensions, new builds and property development. We are very ambitious and would appreciate professional and elegant designs for our new business card.

Very serious about using the services on MakerQuarry and recently acquired our new logo from here :)

Please get involved, i will feedback when i can as i am very busy but can respond daily, thanks

Target Market(s)

People that want to build onto their houses, new building developments or adding too their existing property

Industry/Entity Type

Construction

Contact Information for Business Card

Renwick Tolliver Construction, Lionel Ashby (Managing Director), Tel 07822254961, email - info@renwick-tolliver, www.renwick-tolliver.co.uk

Colors

Designer to choose colors to be used in the design.

Requirements
Must have
• I like a deep grey on the back please. A lot of you have provided black from and back, try mixing things up a little. The black looks cool 😎 Thanks

```html
<!DOCTYPE html>
<html lang="en">
<head>
<meta charset="utf-8">
<title>Renwick Tolliver Construction – Business Card</title>
<link rel="stylesheet" href="https://fonts.googleapis.com/css2?family=Cinzel:wght@400;600&family=Lato:wght@400;700&display=swap">
<style>
  :root {
    --canvas: #2b2b2b;
    --card-black: #1f1f1f;
    --gold-dark: #c4861c;
    --gold-mid: #e6b45a;
    --gold-light: #fbd88c;
    --gold-text: #d9a642;
    --emboss: #3a3a3a;
    --ink: #141414;
  }
  * { margin: 0; padding: 0; box-sizing: border-box; }
  html, body { width: 1200px; height: 1015px; overflow: hidden; }
  body {
    background: var(--canvas);
    display: flex;
    flex-direction: column;
    align-items: center;
    justify-content: center;
    gap: 40px;
    font-family: "Lato", sans-serif;
  }
  .card {
    position: relative;
    width: 760px;
    height: 434px;
    overflow: hidden;
    box-shadow: 0 14px 30px rgba(0,0,0,0.55);
  }

  /* Brand block */
  .brand {
    display: flex;
    flex-direction: column;
    align-items: center;
    gap: 10px;
    font-family: "Cinzel", serif;
    font-weight: 400;
    white-space: nowrap;
  }
  .brand-mark { width: 34px; height: 34px; background: currentColor; }
  .brand-name { font-size: 38px; letter-spacing: 2px; line-height: 1; }
  .brand-sub {
    display: flex;
    align-items: center;
    gap: 12px;
    font-size: 20px;
    letter-spacing: 3px;
    line-height: 1;
  }
  .brand-sub::before, .brand-sub::after {
    content: "";
    width: 36px;
    height: 2px;
    background: currentColor;
  }

  /* Back side */
  .card-back {
    background: var(--card-black);
    display: flex;
    align-items: center;
    justify-content: center;
  }
  .card-back .brand { color: var(--emboss); }

  /* Front side */
  .card-front {
    background: linear-gradient(160deg, var(--gold-dark) 0%, var(--gold-mid) 30%, var(--gold-light) 60%, var(--gold-mid) 85%, var(--gold-dark) 100%);
  }
  .front-shape { position: absolute; inset: 0; }
  .card-front .brand {
    position: absolute;
    left: 400px;
    top: 78px;
    width: 320px;
    color: var(--gold-text);
  }
  .card-front .brand-mark { width: 24px; height: 24px; }
  .card-front .brand-name { font-size: 25px; letter-spacing: 1.5px; }
  .card-front .brand-sub { font-size: 14px; }
  .card-front .brand-sub::before, .card-front .brand-sub::after { width: 28px; }

  .person {
    position: absolute;
    left: 48px;
    top: 176px;
    color: var(--ink);
  }
  .person-name {
    font-family: "Cinzel", serif;
    font-weight: 400;
    font-size: 25px;
    letter-spacing: 1px;
    line-height: 1.1;
  }
  .person-role { font-size: 16px; }

  .contact {
    position: absolute;
    left: 120px;
    top: 270px;
    color: var(--ink);
    font-size: 15px;
    line-height: 1.35;
  }
  .address { margin-bottom: 12px; }
  .contact-list { list-style: none; }
  .contact-list li { display: flex; align-items: center; gap: 8px; }
  .contact-list svg { width: 14px; height: 14px; flex: none; }
</style>
</head>
<body>

  <section class="card card-back" aria-label="Business card back">
    <div class="brand">
      <span class="brand-mark"></span>
      <span class="brand-name">RENWICK TOLLIVER</span>
      <span class="brand-sub">CONSTRUCTION</span>
    </div>
  </section>

  <section class="card card-front" aria-label="Business card front">
    <svg class="front-shape" viewBox="0 0 760 434" aria-hidden="true">
      <defs>
        <linearGradient id="silver-rim" x1="0" y1="0" x2="1" y2="1">
          <stop offset="0" stop-color="#8a8a8a"/>
          <stop offset="0.5" stop-color="#ffffff"/>
          <stop offset="1" stop-color="#9a9a9a"/>
        </linearGradient>
      </defs>
      <circle cx="556" cy="124" r="262" fill="#1c1c1c"/>
      <circle cx="564" cy="118" r="252" fill="url(#silver-rim)"/>
      <circle cx="570" cy="113" r="247" fill="#1f1f1f"/>
    </svg>

    <div class="brand">
      <span class="brand-mark"></span>
      <span class="brand-name">RENWICK TOLLIVER</span>
      <span class="brand-sub">CONSTRUCTION</span>
    </div>

    <div class="person">
      <h1 class="person-name">LIONEL ASHBY</h1>
      <p class="person-role">Managing Director</p>
    </div>

    <div class="contact">
      <p class="address">421 Harrow Lane,<br>Kettering, NN16 8QT</p>
      <ul class="contact-list">
        <li>
          <svg viewBox="0 0 24 24"><path fill="currentColor" d="M6.6 10.8a15 15 0 0 0 6.6 6.6l2.2-2.2a1 1 0 0 1 1-.25 11.4 11.4 0 0 0 3.6.57 1 1 0 0 1 1 1V20a1 1 0 0 1-1 1A17 17 0 0 1 3 4a1 1 0 0 1 1-1h3.5a1 1 0 0 1 1 1c0 1.25.2 2.450.57 3.57a1 1 0 0 1-.25 1z"/></svg>
          07822254961
        </li>
        <li>
          <svg viewBox="0 0 24 24"><path fill="currentColor" d="M2 5h20v14H2zm2 2v.5l8 5 8-5V7l-8 5z"/></svg>
          info@renwick-tolliver.co.uk
        </li>
        <li>
          <svg viewBox="0 0 24 24"><circle cx="12" cy="12" r="9" fill="none" stroke="currentColor" stroke-width="2"/><path d="M3 12h18M12 3c3 3 3 15 0 18M12 3c-3 3-3 15 0 18" fill="none" stroke="currentColor" stroke-width="1.6"/></svg>
          www.renwick-tolliver.co.uk
        </li>
      </ul>
    </div>
  </section>

</body>
</html>
```